Simplified minimalist but bold website

Design a website for a brand 'Brighten Every Day' that shares ideas to make managing home and health easier through email swap series, webinars and eventually courses.

Simple landing page to attract users to sign up for a freebie.

Target Market(s)

women with families & homes to run

Number of Pages Required

1 page

Font styles to use
Sans Serif

Colors
e667a6
b768aa
acd136
ffffff
959595

Requirements
Must have
• Simplified look, line icons, opt-in template, contact us form

```html
<!DOCTYPE html>
<html lang="en">
<head>
<meta charset="utf-8">
<title>Brighten Every Day</title>
<link href="https://fonts.googleapis.com/css2?family=Roboto:wght@300;400;500&display=swap" rel="stylesheet">
<style>
  :root {
    --pink: #e667a6;
    --pink-deep: #d63f8a;
    --berry: #c0206a;
    --mauve: #b768aa;
    --green: #acd136;
    --green-deep: #6f9a1c;
    --blue: #3aa6dd;
    --white: #ffffff;
    --grey: #959595;
    --ink: #333333;
    --footer: #2d2d2d;
  }
  * { box-sizing: border-box; margin: 0; padding: 0; }
  html, body { width: 826px; height: 1200px; overflow: hidden; }
  body { font-family: "Roboto", Arial, sans-serif; background: var(--white); color: var(--ink); position: relative; }

  .hero { position: absolute; left: 0; top: 0; width: 826px; height: 385px; text-align: center; overflow: hidden; }
  .hero__photo { position: absolute; inset: 0; background: linear-gradient(120deg, #5a4a44 0%, #8b7465 35%, #b69a86 55%, #6d5d55 80%, #3f3532 100%); }
  .hero__shade { position: absolute; inset: 0; background: rgba(40, 30, 30, 0.45); }
  .hero__content { position: relative; padding-top: 145px; }
  .hero__title { font-weight: 300; font-size: 32px; color: var(--pink); }
  .hero__tagline { font-weight: 300; font-size: 27px; color: var(--white); margin-top: 10px; }

  .btn { display: inline-block; border-radius: 24px; color: var(--white); font-size: 15px; font-weight: 400; border: none; }
  .btn--hero { background: var(--pink-deep); padding: 11px 30px; margin-top: 20px; }

  .panel { position: absolute; top: 385px; width: 413px; height: 440px; text-align: center; color: var(--white); }
  .panel--swaps { left: 0; background: var(--pink); }
  .panel--guide { left: 413px; background: var(--green); }
  .panel__title { font-weight: 300; font-size: 26px; padding-top: 30px; }
  .panel__rule { width: 60px; height: 2px; background: var(--white); margin: 14px auto 0; }
  .panel__lead { font-size: 14px; font-weight: 500; line-height: 1.5; margin-top: 18px; }
  .panel__text { font-size: 10px; line-height: 1.5; width: 290px; margin: 10px auto 0; opacity: .95; }
  .panel__actions { margin-top: 18px; }
  .btn--small { font-size: 10px; padding: 9px 22px; border-radius: 16px; margin: 0 4px; }
  .btn--green { background: var(--green); }
  .btn--blue { background: var(--blue); }
  .panel__prompt { font-weight: 300; font-size: 18px; margin-top: 20px; }

  .optin { width: 240px; margin: 10px auto 0; }
  .optin__field { display: block; width: 100%; height: 24px; background: var(--white); border: none; margin-bottom: 8px; font-size: 10px; color: var(--grey); text-align: left; padding-left: 6px; line-height: 24px; }
  .btn--form { font-size: 12px; padding: 9px 18px; border-radius: 2px; margin-top: 6px; }
  .btn--berry { background: var(--berry); }
  .btn--leaf { background: var(--green-deep); }

  .guide__visual { width: 200px; height: 150px; margin: 22px auto 12px; background: linear-gradient(135deg, #f4f7ea, #dfe8c4); border-radius: 4px; }

  .series { position: absolute; top: 825px; left: 0; width: 826px; height: 330px; text-align: center; }
  .series__title { font-weight: 300; font-size: 26px; color: var(--grey); padding-top: 32px; }
  .series__text { font-size: 10px; color: var(--grey); line-height: 1.6; width: 430px; margin: 14px auto 0; }
  .series__offer { font-size: 21px; font-weight: 300; color: var(--pink-deep); margin-top: 16px; }
  .series__benefit { font-size: 14px; color: var(--green); margin-top: 4px; }
  .btn--series { background: var(--pink-deep); padding: 11px 28px; margin-top: 20px; font-size: 16px; }

  .footer { position: absolute; top: 1155px; left: 0; width: 826px; height: 45px; background: var(--footer); color: #cfcfcf; font-size: 10px; text-align: center; line-height: 45px; }
  .footer__top { position: absolute; right: 40px; top: 14px; width: 16px; height: 16px; }
</style>
</head>
<body>
  <header class="hero">
    <div class="hero__photo" role="img" aria-label="Photo of a smiling family gathered together at home"></div>
    <div class="hero__shade"></div>
    <div class="hero__content">
      <h1 class="hero__title">Brighten Every Day</h1>
      <p class="hero__tagline">Chances are life is a little overwhelming</p>
      <span class="btn btn--hero">Let us Help</span>
    </div>
  </header>

  <section class="panel panel--swaps">
    <h2 class="panel__title">Swaps Email Series</h2>
    <div class="panel__rule"></div>
    <p class="panel__lead">Save TIME, MONEY &amp; SANITY with<br>simple product swaps</p>
    <p class="panel__text">Discover the easiest ways to cut your clutter, swap tricky products for better choices and win back your time, budget and calm.</p>
    <div class="panel__actions">
      <span class="btn btn--small btn--green">SEE SAMPLE SWAP</span>
      <span class="btn btn--small btn--blue">LEARN MORE</span>
    </div>
    <p class="panel__prompt">Send your ideas my way...</p>
    <form class="optin">
      <span class="optin__field">Name</span>
      <span class="optin__field">Email</span>
      <span class="btn btn--form btn--berry">Send Me The Guide!</span>
    </form>
  </section>

  <section class="panel panel--guide">
    <h2 class="panel__title">Decluttering Guide</h2>
    <div class="panel__rule"></div>
    <div class="guide__visual" role="img" aria-label="Illustration of two decluttering guide booklets"></div>
    <form class="optin">
      <span class="optin__field">Name</span>
      <span class="optin__field">Email</span>
      <span class="btn btn--form btn--leaf">Sign Me Up!</span>
    </form>
  </section>

  <section class="series">
    <h2 class="series__title">Swaps Email Series</h2>
    <p class="series__text">Each week we share one simple product swap to lighten your load at home, from kitchen staples to cleaning picks, plus quick tips you can try today.</p>
    <p class="series__offer">You get an email 2x weekly for 6-12 weeks only</p>
    <p class="series__benefit">Get more done in less time and feel your best every day</p>
    <p class="series__text">Join our simple swap series and get tips delivered to your inbox. Better yet, come along with a friend and grow together.</p>
    <span class="btn btn--series">Sign Me Up!</span>
  </section>

  <footer class="footer">
    © Copyright 2018 Brighten Every Day All rights reserved.
    <svg class="footer__top" viewBox="0 0 16 16" aria-hidden="true"><path d="M3 10 L8 5 L13 10" fill="none" stroke="#cfcfcf" stroke-width="1.6"/></svg>
  </footer>
</body>
</html>
```